Business Card for Fashion House

We need a business card design for our personalize fashion service for our customers. the business card should reflect reliability, luxury and creativity.
The brand Gravetto is extracted from "Graceful Velvetto"; Gravetto provides fashion designs sprinkled with luxury and style tailored for our elite clients character profile.
Gravetto is created for those who embody class and elegance with a passion for style.
Target Market(s)
Affluent Customers
Industry/Entity Type
Fashion
Contact Information for Business Card
Samira Haddadin
Fashion Designer
Telephone: +971 4 555 0192
Mobile +971 50 555 0147
Emal info@gravetto-example.com
Website www.gravetto-example.com
Social Media Youtube g+ Facebook Instagram Pin /gravetto
Font styles to use
Other font styles liked:
- Audrey provided
Look and feel
Each slider illustrates characteristics of the customer's brand and the style your logo design should communicate.

```html
<!DOCTYPE html>
<html lang="en">
<head>
<meta charset="utf-8">
<title>Gravetto – Business Card</title>
<link rel="stylesheet" href="https://fonts.googleapis.com/css2?family=Josefin+Sans:wght@300&family=Marcellus&family=Roboto:wght@400&display=swap">
<style>
  :root {
    --page: #d9d4cf;
    --card-light: #f6f3f0;
    --card-mid: #e7e1dc;
    --ink: #231f1e;
    --ink-soft: #3a3533;
    --band-top: #5a524e;
    --contact: #dccbb6;
    --icon: #e6dccf;
  }
  * { margin: 0; padding: 0; box-sizing: border-box; }
  html, body {
    width: 1200px; height: 1054px; overflow: hidden;
    background: var(--page);
  }
  .card {
    position: absolute;
    left: 80px; top: 213px;
    width: 1040px; height: 628px;
    background: linear-gradient(160deg, var(--card-light), var(--card-mid));
    overflow: hidden;
    box-shadow: 0 10px 30px rgba(0,0,0,.12);
  }
  .accent-band {
    position: absolute; left: 0; right: 0; top: 412px; bottom: 0;
    background: linear-gradient(180deg, var(--band-top) 0%, var(--ink) 45%, var(--ink) 100%);
  }
  .brand-wordmark {
    position: absolute; left: 97px; top: 254px;
    font-family: "Josefin Sans", sans-serif; font-weight: 300;
    font-size: 52px; letter-spacing: 14px;
    color: var(--ink);
  }
  .social-handle {
    position: absolute; left: 156px; top: 352px;
    display: flex; align-items: center; gap: 10px;
    font-family: "Roboto", sans-serif; font-size: 26px;
    color: var(--ink-soft);
  }
  .social-dot {
    width: 22px; height: 22px; border-radius: 50%;
    background: var(--ink-soft);
  }
  .holder {
    position: absolute; right: 61px; top: 80px; text-align: right;
  }
  .holder-name {
    font-family: "Marcellus", serif; font-weight: 400; font-size: 42px;
    color: var(--ink); line-height: 1.1;
  }
  .holder-role {
    font-family: "Roboto", sans-serif; font-size: 21px;
    color: var(--ink-soft); margin-top: 8px;
  }
  .contact-list {
    position: absolute; right: 52px; top: 436px;
    list-style: none;
  }
  .contact-item {
    display: flex; justify-content: flex-end; align-items: center;
    gap: 16px; height: 35px;
    font-family: "Roboto", sans-serif; font-size: 25px;
    color: var(--contact);
  }
  .contact-icon { width: 26px; height: 26px; flex: none; }
</style>
</head>
<body>
  <main class="card">
    <div class="accent-band" role="img" aria-label="Dark decorative wave band along the lower edge of the card"></div>

    <div class="brand-wordmark">GRAVETTO</div>

    <div class="social-handle"><span class="social-dot"></span>/gravetto</div>

    <header class="holder">
      <h1 class="holder-name">Samira Haddadin</h1>
      <p class="holder-role">Fashion Designer</p>
    </header>

    <ul class="contact-list">
      <li class="contact-item">+971 4 555 0192
        <svg class="contact-icon" viewBox="0 0 24 24" fill="none" stroke="var(--icon)" stroke-width="1.6"><circle cx="12" cy="12" r="10"/><path d="M8.5 7.5l2 2-1 1.5c.8 1.6 2 2.8 3.5 3.5l1.5-1 2 2-1.3 1.5C11 16.5 7.5 13 7 8.8z"/></svg>
      </li>
      <li class="contact-item">+971 50 555 0147
        <svg class="contact-icon" viewBox="0 0 24 24" fill="none" stroke="var(--icon)" stroke-width="1.6"><rect x="7" y="2.5" width="10" height="19" rx="2"/><line x1="10.5" y1="18.5" x2="13.5" y2="18.5"/></svg>
      </li>
      <li class="contact-item">info@gravetto-example.com
        <svg class="contact-icon" viewBox="0 0 24 24" fill="none" stroke="var(--icon)" stroke-width="1.6"><rect x="3" y="5.5" width="18" height="13" rx="1"/><path d="M3 6l9 7 9-7"/></svg>
      </li>
      <li class="contact-item">www.gravetto-example.com
        <svg class="contact-icon" viewBox="0 0 24 24" fill="none" stroke="var(--icon)" stroke-width="1.6"><circle cx="12" cy="12" r="9.5"/><ellipse cx="12" cy="12" rx="4" ry="9.5"/><line x1="2.5" y1="12" x2="21.5" y2="12"/><path d="M4.5 7h15M4.5 17h15"/></svg>
      </li>
    </ul>
  </main>
</body>
</html>
```